Tampa Bay fishing guide needs stunning website.

I currently have a site - www.reelcoveguide.net which I personally put together using the Pagely platform and I am looking for a redesign on a different platform (Sitecraft?) that will allow me to easily create landing pages in the future. Would like to have a block for visitors to opt in to newsletter. Need social media links on all pages.

I would like to let my visitors know that I am able to handle their fishing charter needs here in the Tampa Bay area, if I'm not available for the dates they are looking to go I can refer them to a reputable captain in the area.

Target Market(s)

United States

Industry/Entity Type

Tourism

Coding

Coded - Design and coding required

Number of Pages Required

5+ page

Font styles to use
Sans Serif

Colors
0355a3
3176b5
85abd2
fbf289

Requirements
Must have
• Mobile Responsive, Ability to insert Vantor Metrics, Chatterbox pixels, ability to add custom landing pages in future
Nice to have
• Clean, easy navigation

```html
<!DOCTYPE html>
<html lang="en">
<head>
<meta charset="utf-8">
<title>Capt. Dale Harlow – Tampa Bay Fishing Charters</title>
<link rel="stylesheet" href="https://fonts.googleapis.com/css2?family=Uncial+Antiqua&family=Roboto:wght@400;500;700&family=Cormorant+Garamond:ital,wght@1,500&display=swap">
<style>
:root{
  --blue:#1c69d6;
  --blue-dark:#0355a3;
  --blue-mid:#3176b5;
  --blue-light:#85abd2;
  --yellow:#fbf289;
  --yellow-bg:#f5ec8a;
  --ink:#1e1e1e;
  --grey:#6b6b6b;
  --card:#e9e9e9;
  --white:#ffffff;
}
*{box-sizing:border-box;margin:0;padding:0}
html,body{width:1200px;height:3046px;overflow:hidden}
body{font-family:"Roboto",Arial,sans-serif;color:var(--ink);background:var(--white);position:relative}
.abs{position:absolute}
.display{font-family:"Uncial Antiqua",Georgia,serif;font-weight:400}

/* hero */
.hero{left:0;top:0;width:1200px;height:570px;background:radial-gradient(ellipse at 72% 50%,#2f5f86 0%,#10273b 45%,#050c14 100%)}
.nav-rule{left:0;top:115px;width:1200px;height:2px;background:var(--blue-mid)}
.brand{left:98px;top:38px;display:flex;align-items:center;gap:12px;color:var(--white);font-size:40px}
.brand-dot{width:26px;height:26px;border-radius:50%;background:var(--white)}
.nav{right:98px;top:46px;display:flex;gap:50px;list-style:none}
.nav a{color:var(--white);text-decoration:none;font-size:17px;font-weight:500;letter-spacing:.3px;position:relative}
.nav .active::after{content:"";position:absolute;left:0;top:30px;width:46px;height:3px;background:var(--yellow);transform:skewX(-30deg)}
.hero-title{left:98px;top:190px;color:var(--white);font-size:62px;line-height:1.15}
.hero-sub{left:98px;top:346px;color:var(--white);font-size:24px;font-weight:700}
.btn-yellow{left:98px;top:412px;width:148px;height:56px;background:var(--yellow);color:var(--blue-dark);font-family:"Uncial Antiqua",serif;font-size:20px;display:flex;align-items:center;justify-content:center}
.arrow{top:290px}

/* search band */
.search{left:0;top:560px;width:1200px;height:150px}
.search-row{left:98px;top:593px;display:flex;align-items:center;gap:8px}
.search-label{color:var(--white);font-size:23px;font-weight:700;margin-right:8px}
.field{height:48px;background:var(--white);font-size:15px;color:var(--ink);display:flex;align-items:center;justify-content:space-between;padding:0 12px}
.btn-search{width:178px;height:48px;background:var(--yellow);color:var(--blue-dark);font-size:15px;font-weight:700;display:flex;align-items:center;justify-content:center;border:2px solid #fff7b0}

/* welcome */
.welcome-title{left:98px;top:768px;font-size:36px;color:var(--ink)}
.blue-word{color:var(--blue)}
.welcome-sub{left:98px;top:836px;font-size:20px;font-weight:500;letter-spacing:.3px}
.welcome-text{left:98px;top:876px;width:650px;font-size:13px;line-height:24px;color:var(--grey)}
.welcome-text p{margin-bottom:12px}
.welcome-text a{color:var(--blue-dark);font-weight:700}
.btn-blue{background:var(--blue);color:var(--white);font-size:15px;font-weight:500;display:flex;align-items:center;justify-content:center}
.welcome-btn{left:98px;top:1062px;width:118px;height:44px}
.welcome-photo{left:772px;top:775px;width:330px;height:334px;border-radius:6px;background:linear-gradient(160deg,#7aa4c4,#3d6a8a 60%,#dcd6c8)}

/* sharing */
.share{left:0;top:1165px;width:1200px;height:455px;background:linear-gradient(120deg,#1a64cc,#2b78dc 50%,#1c69d6)}
.share-title{left:0;top:1222px;width:1200px;text-align:center;color:var(--white);font-size:32px}
.feature{top:1320px;width:300px;text-align:center;color:var(--white)}
.feature svg{display:block;margin:0 auto 22px}
.feature h3{font-size:22px;font-weight:500;margin-bottom:16px}
.feature.highlight h3{color:var(--yellow)}
.feature p{font-size:14.5px;line-height:26px}

/* rates */
.rates-title{left:0;top:1668px;width:1200px;text-align:center;font-size:32px}
.card{top:1748px;width:313px;height:427px;background:var(--card);box-shadow:0 3px 4px rgba(0,0,0,.18)}
.card-photo{height:198px}
.price{position:absolute;left:0;top:227px;width:58px;height:68px;background:var(--blue);color:var(--white);text-align:center;font-weight:700;font-size:22px;line-height:26px;padding-top:8px}
.price.light{background:var(--blue-light)}
.card-body{position:absolute;left:76px;top:225px;width:225px}
.card-kicker{font-size:13px;color:#333}
.card-name{font-size:17px;font-weight:700;margin:6px 0 6px}
.card-text{font-size:13px;line-height:22px;color:var(--grey)}
.card-btn{position:absolute;left:77px;top:359px;width:103px;height:40px;font-size:14px}
.card-btn.light{background:var(--blue-light)}

/* testimonials */
.testi{left:0;top:2220px;width:1200px;height:480px;background:var(--yellow-bg)}
.testi-title{left:0;top:2280px;width:1200px;text-align:center;font-size:32px;color:var(--blue)}
.quote{left:236px;top:2370px;width:728px;text-align:center;font-family:"Cormorant Garamond",Georgia,serif;font-style:italic;font-size:22px;line-height:42px;color:#333}
.quote-mark{font-family:Georgia,serif;font-size:80px;color:var(--blue);line-height:1}
.quote-name{left:0;top:2474px;width:1200px;text-align:center;font-size:18px;color:#333}
.btn-outline{left:489px;top:2530px;width:222px;height:48px;border:2px solid var(--blue);border-radius:24px;color:var(--blue);font-size:16px;display:flex;align-items:center;justify-content:center}

/* footer */
.footer-wave{left:0;top:2600px;width:1200px;height:120px}
.footer{left:0;top:2700px;width:1200px;height:285px;background:var(--blue)}
.footer-brand{left:98px;top:2800px;display:flex;align-items:center;gap:12px;color:var(--white);font-size:40px}
.footer-col h4{color:var(--white);font-size:16px;font-weight:700;letter-spacing:.3px;margin-bottom:24px}
.links{list-style:none}
.links li{color:var(--white);font-size:14px;margin-bottom:14px}
.contact-item{display:flex;gap:16px;margin-bottom:18px;color:var(--white);font-size:13.5px;line-height:20px}
.contact-item b{display:block;font-size:14px}
.ring{width:38px;height:38px;border:2px solid var(--white);border-radius:50%;flex:none;display:flex;align-items:center;justify-content:center}
.input{height:38px;border:1.5px solid var(--white);border-radius:4px;color:var(--white);font-size:12px;padding:10px 10px}
.btn-signup{width:118px;height:38px;background:var(--blue-dark);border:1.5px solid var(--white);color:var(--white);font-size:12px;font-weight:700;display:flex;align-items:center;justify-content:center}
.bottom-bar{left:0;top:2985px;width:1200px;height:61px;background:#0d52b8;color:var(--white);font-size:13px}
.copyright{left:98px;top:22px}
.socials{right:118px;top:12px;display:flex;gap:10px}
.social{width:36px;height:36px;border:2px solid var(--white);border-radius:50%}
</style>
</head>
<body>

<!-- hero -->
<div class="abs hero" role="img" aria-label="Photo: smiling angler on a boat at night holding a bent fishing rod with a tarpon splashing"></div>
<div class="abs nav-rule"></div>
<div class="abs brand display"><span class="brand-dot"></span>Harlow</div>
<ul class="abs nav">
  <li><a class="active" href="#">HOME</a></li>
  <li><a href="#">ABOUT US</a></li>
  <li><a href="#">PICKUP LOCATIONS</a></li>
  <li><a href="#">RATES</a></li>
  <li><a href="#">CONTACT</a></li>
</ul>
<h1 class="abs hero-title display">Your Fishing<br>Adventure Awaits</h1>
<div class="abs hero-sub">Tampa Bay Fishing Charters Florida</div>
<div class="abs btn-yellow">Read More</div>
<svg class="abs arrow" style="left:28px" width="24" height="48" viewBox="0 0 24 48"><polyline points="22,2 2,24 22,46" fill="none" stroke="#fff" stroke-width="2.5"/></svg>
<svg class="abs arrow" style="right:28px" width="24" height="48" viewBox="0 0 24 48"><polyline points="2,2 22,24 2,46" fill="none" stroke="#fff" stroke-width="2.5"/></svg>

<!-- search band -->
<svg class="abs search" viewBox="0 0 1200 150" preserveAspectRatio="none">
  <path d="M0 0H1200V95C1050 60 950 120 780 105C600 90 500 60 330 95C200 120 90 110 0 95Z" fill="#1c69d6"/>
</svg>
<div class="abs search-row">
  <span class="search-label">Start Your Fishing:</span>
  <div class="field" style="width:198px">Your Destination <span>▾</span></div>
  <div class="field" style="width:198px">Start Date <span>▦</span></div>
  <div class="field" style="width:198px">End Date <span>▦</span></div>
  <div class="btn-search">SEARCH CHARTERS</div>
</div>

<!-- welcome -->
<h2 class="abs welcome-title display">Welcome to <span class="blue-word">Harlow</span></h2>
<div class="abs welcome-sub">TAMPA BAY, FISHING GUIDE, TAMPA BAY FISHING CHARTERS</div>
<div class="abs welcome-text">
  <p>Capt. Dale Harlow, with over 20 years' experience, Native fishing charter tampa charter captain offering full and half day fishing charters on the waters of Tampa Bay. If you're looking for a great fishing charter tampa don't hesitate to contact Capt. Dale or you can simply book your trip online <a href="#">here.</a></p>
  <p>Come enjoy a wonderful day fishing charters Tampa for Tarpon, Snook, Redfish, Trout, Sharks, Cobia, Spanish mackerel as well as others aboard Capt. Dale Harlow Sport fishing Charters boat. Capt. Dale will work hard to ensure that you and your guests have a memorable day enjoying the wonderful gamefish that Tampa Bay</p>
</div>
<div class="abs btn-blue welcome-btn">Read More</div>
<div class="abs welcome-photo" role="img" aria-label="Photo: two anglers on a boat holding up a large tarpon"></div>

<!-- sharing -->
<div class="abs share" role="img" aria-label="Blue tinted photo of anglers fishing from a boat"></div>
<h2 class="abs share-title display">Sharing a Charter is Easy</h2>
<div class="abs feature" style="left:94px">
  <svg width="90" height="90" viewBox="0 0 90 90"><rect x="22" y="6" width="54" height="78" rx="6" fill="#fff"/><rect x="12" y="18" width="18" height="7" rx="3" fill="#fff" stroke="#1c69d6" stroke-width="3"/><rect x="12" y="40" width="18" height="7" rx="3" fill="#fff" stroke="#1c69d6" stroke-width="3"/><rect x="12" y="62" width="18" height="7" rx="3" fill="#fff" stroke="#1c69d6" stroke-width="3"/><rect x="40" y="20" width="24" height="12" rx="2" fill="#1c69d6"/></svg>
  <h3>BOOK A SPOT</h3>
  <p>Capt. Dale invites you and your guests to come aboard and enjoy the thrills of fishing for the top gamefish that Tampa Bay.</p>
</div>
<div class="abs feature highlight" style="left:453px">
  <svg width="90" height="90" viewBox="0 0 90 90"><polygon points="46,4 46,52 74,52" fill="#fbf289"/><polygon points="40,14 40,52 18,52" fill="#fbf289"/><path d="M10 58H80L70 72H20Z" fill="#fbf289"/><path d="M8 80Q18 74 28 80T48 80T68 80T84 80" fill="none" stroke="#fbf289" stroke-width="4"/></svg>
  <h3>SHARE THE BOAT</h3>
  <p>Capt. Dale invites you and your guests to come aboard and enjoy the thrills of fishing for the top gamefish that Tampa Bay.</p>
</div>
<div class="abs feature" style="left:810px">
  <svg width="90" height="90" viewBox="0 0 90 90"><text x="45" y="44" text-anchor="middle" font-family="Roboto,sans-serif" font-weight="700" font-size="46" fill="#fff">$</text><path d="M8 64H28L42 60H62C66 60 66 67 62 67H44M46 67H64L80 56C85 53 88 59 84 63L66 78H8Z" fill="#fff"/></svg>
  <h3>LOWER THE PRICE</h3>
  <p>Capt. Dale invites you and your guests to come aboard and enjoy the thrills of fishing for the top gamefish that Tampa Bay.</p>
</div>

<!-- rates -->
<h2 class="abs rates-title display">Fishing <span class="blue-word">Rates</span></h2>

<div class="abs card" style="left:98px">
  <div class="card-photo" role="img" aria-label="Photo: angler in blue shirt holding a snook" style="background:linear-gradient(180deg,#8fb3cf,#3f6f3e 55%,#e6eef2)"></div>
  <div class="price">$<br>499</div>
  <div class="card-body">
    <div class="card-kicker">Fishing Rates</div>
    <div class="card-name">Half Day (4 hour) Charter</div>
    <div class="card-text">Enjoy a half day trip on the beautiful waters of Tampa Bay. Trip includes all bait, tackle and licenses.</div>
  </div>
  <div class="btn-blue card-btn">Read More</div>
</div>

<div class="abs card" style="left:445px">
  <div class="card-photo" role="img" aria-label="Photo: young woman holding a spotted sea trout over calm water" style="background:linear-gradient(180deg,#b9d3ea,#7aa6c6 55%,#5d8fae)"></div>
  <div class="price light">$<br>599</div>
  <div class="card-body">
    <div class="card-kicker">Fishing Rates</div>
    <div class="card-name">Donec quis ex vel tincidunt</div>
    <div class="card-text">Enjoy a half day trip on the beautiful waters of Tampa Bay. Trip includes all bait, tackle and licenses.</div>
  </div>
  <div class="btn-blue card-btn light">Read More</div>
</div>

<div class="abs card" style="left:790px">
  <div class="card-photo" role="img" aria-label="Photo: two anglers casting rods from a boat" style="background:linear-gradient(180deg,#c9dff0,#a6c3d8 60%,#7f9fb6)"></div>
  <div class="price light">$<br>699</div>
  <div class="card-body">
    <div class="card-kicker">Fishing Rates</div>
    <div class="card-name">Donec quis ex vel tincidunt</div>
    <div class="card-text">Enjoy a half day trip on the beautiful waters of Tampa Bay. Trip includes all bait, tackle and licenses.</div>
  </div>
  <div class="btn-blue card-btn light">Read More</div>
</div>

<!-- testimonials -->
<div class="abs testi" role="img" aria-label="Faint yellow tinted photo of anglers on a boat"></div>
<h2 class="abs testi-title display">Read Our Testimonials</h2>
<div class="abs quote-mark" style="left:166px;top:2345px">“</div>
<div class="abs quote">Our most popular and recommended trip. Enjoy a 6 hour trip on the beautiful waters of Tampa Bay. Trip includes all bait, tackle and licenses.</div>
<div class="abs quote-mark" style="left:952px;top:2420px">”</div>
<div class="abs quote-name">Mara T. Charter</div>
<div class="abs btn-outline">Read More Testimonials</div>

<!-- footer -->
<svg class="abs footer-wave" viewBox="0 0 1200 120" preserveAspectRatio="none">
  <path d="M0 40C180 90 380 100 560 70C760 36 900 20 1060 40C1120 48 1170 50 1200 46V120H0Z" fill="#1c69d6"/>
</svg>
<div class="abs footer"></div>
<div class="abs footer-brand display"><span class="brand-dot"></span>Harlow</div>

<div class="abs footer-col" style="left:418px;top:2706px">
  <h4>QUICK LINKS</h4>
  <ul class="links">
    <li>› Home</li><li>› About Us</li><li>› Pickup Loactions</li><li>› Rates</li><li>› Gift Card</li><li>› Contact Us</li>
  </ul>
</div>

<div class="abs footer-col" style="left:603px;top:2706px;width:210px">
  <h4>CONTACT US</h4>
  <div class="contact-item"><span class="ring"><svg width="14" height="18" viewBox="0 0 14 18"><path d="M7 1C3.7 1 1 3.6 1 7C1 11 7 17 7 17S13 11 13 7C13 3.6 10.3 1 7 1Z" fill="none" stroke="#fff" stroke-width="2"/><circle cx="7" cy="7" r="2" fill="#fff"/></svg></span><div><b>HARLOW,</b>Bayside Marina - St. Petersburg</div></div>
  <div class="contact-item"><span class="ring"><svg width="12" height="18" viewBox="0 0 12 18"><rect x="1" y="1" width="10" height="16" rx="2" fill="none" stroke="#fff" stroke-width="2"/><circle cx="6" cy="14" r="1" fill="#fff"/></svg></span><div><b>PHONE:</b>555-014-2290</div></div>
  <div class="contact-item"><span class="ring"><svg width="18" height="12" viewBox="0 0 18 12"><rect x="1" y="1" width="16" height="10" fill="none" stroke="#fff" stroke-width="2"/><polyline points="1,1 9,7 17,1" fill="none" stroke="#fff" stroke-width="2"/></svg></span><div><b>Mail:</b>captdale@harlowcharters.net</div></div>
</div>

<div class="abs footer-col" style="left:830px;top:2706px;width:272px">
  <h4>NEWSLETTER SIGNUP</h4>
  <div style="display:flex;gap:8px;margin-bottom:8px">
    <div class="input" style="width:130px">Name</div>
    <div class="input" style="width:134px">Phone</div>
  </div>
  <div class="input" style="width:272px;margin-bottom:14px">Email Address</div>
  <div class="btn-signup">SIGNUP NOW</div>
</div>

<div class="abs bottom-bar">
  <div class="abs copyright">Copyright © 2016 Harlow. All Right Reserved</div>
  <div class="abs socials">
    <span class="social"></span><span class="social"></span><span class="social"></span><span class="social"></span><span class="social"></span>
  </div>
</div>

</body>
</html>
```